WP website design (Harrowgate)

We need a wordpress design for an established auction and real estate company based in Florida. The winning design will incorporate a professional color scheme with company logo in a clean layout. The design needs to consider that this will be developed on a responsive theme. Colors are those that will highlight the logo.

Industry/Entity Type

Real Estate

Font styles to use
Serif
Sans Serif

Colors

Designer to choose colors to be used in the design.

Requirements
Must have
• Navigation:
1) Home
2) Auctions
3) Online Auctions
4) About Us
5) Services
6) Real Estate Listings
7) References
8) Contact Us

Colors will be blue (#000066) / red (#B10000) and black or other complementary color. Tagline to be used "Since 1977, Proven Results." Slideshow to be placed in the header or body of home page - please use stock real estate image.

Widgets: 1) Email Sign-up 2) Social media icons for FB and LinkedIn 3) Featured Listings 4) Testimonials 5) Register button

Footer will have smaller company logo, attached logos and contact info:
Phone: (555) 261-0948 Mobile: (555) 718-3062
Email: mirelharrowgate@quellmail.example
Address: 58 E. Tamsin Avenue, Ste 410, Pensacola, FL 32599
Nice to have
• Use of a drop down menu:
Auctions-
1) Upcoming Auctions
2) Past Auctions

```html
<!DOCTYPE html>
<html lang="en">
<head>
<meta charset="utf-8">
<title>Harrowgate Auctions</title>
<link href="https://fonts.googleapis.com/css2?family=Open+Sans:ital,wght@0,400;0,600;0,700;1,700&display=swap" rel="stylesheet">
<style>
:root{
  --navy:#1f2a8c;
  --red:#d3222a;
  --red-dark:#b10000;
  --ink:#333;
  --muted:#8a8a8a;
  --rule:#e6e6e6;
  --dark:#2f3137;
  --charcoal:#3b3b3b;
  --star:#f2a51a;
  --orange:#ffb400;
  --foot:#f1f1f1;
}
*{box-sizing:border-box;margin:0;padding:0}
html,body{width:808px;height:1200px;overflow:hidden;background:#fff}
body{position:relative;font-family:"Open Sans",Arial,sans-serif;color:var(--ink)}
.abs{position:absolute}

/* header */
.brand{left:121px;top:14px;display:flex;align-items:center;gap:10px}
.brand-mark{width:40px;height:40px;background:var(--red)}
.brand-name{font-size:24px;font-weight:700;color:var(--navy);letter-spacing:-.3px}
.social-top{left:561px;top:25px;display:flex;gap:6px}
.social-top span{width:18px;height:18px;border:1px solid #ddd;border-radius:50%;display:block}
.register-top{left:612px;top:21px;width:74px;height:25px;background:#f0f0f0;font-size:8px;display:flex;align-items:center;justify-content:center;gap:6px;color:#444}

/* nav */
.nav{left:0;top:70px;width:808px;height:34px;background:var(--red);border-bottom:2px solid #444}
.nav-home{left:121px;top:70px;width:36px;height:34px;background:#4a4a4a;display:flex;align-items:center;justify-content:center}
.nav-item{top:70px;height:34px;line-height:34px;font-size:8.6px;color:#fff}
.nav-item.active{color:var(--orange)}
.nav-sep{top:78px;width:1px;height:18px;background:rgba(0,0,0,.15)}
.dropdown{left:156px;top:104px;width:128px;height:62px;background:var(--red)}
.dropdown a{position:absolute;left:11px;font-size:8px;color:#fff;text-decoration:none}
.dropdown .rule{position:absolute;left:0;top:29px;width:128px;height:1px;background:rgba(0,0,0,.12)}

/* slider */
.hero{left:121px;top:114px;width:565px;height:288px;background:linear-gradient(180deg,#4a3a6a 0%,#b0506a 30%,#6a4a6a 55%,#3a3050 72%,#7a4a5a 100%)}
.hero-arrow{top:263px;width:17px;height:17px;border-radius:50%;background:rgba(255,255,255,.85);display:flex;align-items:center;justify-content:center}
.tagline{left:121px;top:333px;width:565px;text-align:center;font-size:20px;font-weight:700;font-style:italic;color:#fff;text-shadow:0 1px 3px rgba(0,0,0,.5)}

/* featured */
.section-title{font-size:14px;color:#333}
.pager{top:426px;width:13px;height:13px;border:1px solid #ddd;border-radius:50%;display:flex;align-items:center;justify-content:center}
.card{top:454px;width:130px}
.card-photo{width:130px;height:120px}
.card-title{margin-top:8px;font-size:10.4px;color:#333}
.stars{margin-top:6px;height:8px}
.card-text{margin-top:5px;font-size:6.6px;line-height:12px;color:var(--muted);text-align:justify}

/* list banner */
.cta{left:121px;top:681px;width:566px;height:58px;background:linear-gradient(90deg,#3a2f29,#6a4c36 50%,#3d322c)}
.cta-title{left:147px;top:689px;font-size:14.5px;color:#fff;font-weight:600}
.cta-sub{left:147px;top:715px;font-size:10px;color:#fff}
.cta-btn{left:575px;top:695px;width:81px;height:31px;border:1px solid rgba(255,255,255,.45);color:#fff;font-size:13px;display:flex;align-items:center;justify-content:center}

/* testimonials & news */
.rule{height:1px;background:var(--rule)}
.avatar{width:72px;height:72px;border-radius:50%;border:3px solid #eee;background:linear-gradient(180deg,#c9b8a8,#8a7a70)}
.item-title{font-size:8.2px;color:#333}
.item-sub{font-size:6.4px;color:var(--muted)}
.item-text{font-size:6.5px;line-height:12px;color:var(--muted);text-align:justify}
.date{font-size:6.6px;color:#333;display:flex;align-items:center;gap:5px}
.news-photo{width:98px;height:79px}

.skyline{left:0;top:985px;width:808px;height:57px;background:linear-gradient(180deg,rgba(235,235,235,0),rgba(230,230,230,.7))}

/* newsletter */
.newsletter{left:0;top:1042px;width:808px;height:76px;background:var(--dark)}
.nl-title{left:122px;top:1055px;font-family:Arial,sans-serif;font-size:22px;font-weight:700;color:#fff}
.nl-sub{left:122px;top:1086px;font-family:Arial,sans-serif;font-size:10px;color:#fff}
.nl-label{top:1057px;font-family:Arial,sans-serif;font-size:7.5px;color:#fff}
.nl-input{top:1075px;width:105px;height:29px;background:#fff;border-radius:2px}
.nl-btn{left:595px;top:1075px;width:93px;height:29px;background:#111;color:#fff;font-family:Arial,sans-serif;font-size:10px;display:flex;align-items:center;justify-content:center}

/* footer */
.footer{left:0;top:1118px;width:808px;height:82px;background:var(--foot)}
.copyright{left:122px;top:1154px;font-family:Arial,sans-serif;font-size:6.8px;color:#333}
.badge{background:#d9d9d9;border-radius:2px}
.badge.white{background:#fff;border:1px solid #e0e0e0}
.foot-social{top:1152px;width:13px;height:13px;border-radius:50%;background:#2a66b8}
</style>
</head>
<body>

<!-- header -->
<div class="abs brand"><span class="brand-mark"></span><span class="brand-name">Harrowgate</span></div>
<div class="abs social-top" aria-label="Social links"><span></span><span></span></div>
<div class="abs register-top">
  <svg width="11" height="11" viewBox="0 0 11 11"><circle cx="5.5" cy="3.3" r="2.5" fill="#777"/><path d="M1 11c0-3 2-4.5 4.5-4.5S10 8 10 11z" fill="#777"/></svg>
  Register
</div>

<!-- navigation -->
<div class="abs nav"></div>
<div class="abs nav-home">
  <svg width="16" height="14" viewBox="0 0 16 14"><path d="M8 0 0 7h2v7h4V9h4v5h4V7h2z" fill="#fff"/></svg>
</div>
<div class="abs nav-item active" style="left:181px">Auctions</div>
<div class="abs nav-sep" style="left:229px"></div>
<div class="abs nav-item" style="left:242px">Online Auctions</div>
<div class="abs nav-sep" style="left:314px"></div>
<div class="abs nav-item" style="left:326px">About Us</div>
<div class="abs nav-sep" style="left:376px"></div>
<div class="abs nav-item" style="left:390px">Services</div>
<div class="abs nav-sep" style="left:433px"></div>
<div class="abs nav-item" style="left:446px">Real Estate Listings</div>
<div class="abs nav-sep" style="left:533px"></div>
<div class="abs nav-item" style="left:546px">References</div>
<div class="abs nav-sep" style="left:601px"></div>
<div class="abs nav-item" style="left:614px">Contact Us</div>

<div class="abs hero" role="img" aria-label="City skyline at dusk reflected in water"></div>
<div class="abs hero-arrow" style="left:156px"><svg width="6" height="8" viewBox="0 0 6 8"><path d="M5 1 2 4l3 3" stroke="#666" stroke-width="1.4" fill="none"/></svg></div>
<div class="abs hero-arrow" style="left:630px"><svg width="6" height="8" viewBox="0 0 6 8"><path d="M1 1l3 3-3 3" stroke="#666" stroke-width="1.4" fill="none"/></svg></div>
<div class="abs tagline">Since 1977, Proven Results</div>

<div class="abs dropdown">
  <a style="top:12px">Upcoming Auctions</a>
  <span class="rule"></span>
  <a style="top:41px">Past Auctions</a>
</div>

<!-- featured listings -->
<div class="abs section-title" style="left:121px;top:421px">Featured Listings</div>
<div class="abs pager" style="left:657px"><svg width="5" height="6" viewBox="0 0 5 6"><path d="M3.5 1 1.5 3l2 2" stroke="#555" fill="none"/></svg></div>
<div class="abs pager" style="left:675px"><svg width="5" height="6" viewBox="0 0 5 6"><path d="M1.5 1l2 2-2 2" stroke="#555" fill="none"/></svg></div>

<div class="abs card" style="left:122px">
  <div class="card-photo" role="img" aria-label="Stone cottage with garden" style="background:linear-gradient(180deg,#9aa0a4,#8a6a4a 55%,#4e7a2e)"></div>
  <div class="card-title">Donec lacinia lacus</div>
  <svg class="stars" width="40" height="8" viewBox="0 0 40 8"><g fill="#f2a51a"><path id="s" d="M4 0l1 2.6 2.8.2-2.2 1.8.7 2.8L4 5.9 1.7 7.4l.7-2.8L.2 2.8 3 2.6z"/><use href="#s" x="8"/><use href="#s" x="16"/></g><g fill="none" stroke="#f2a51a" stroke-width=".6"><use href="#s" x="24"/><use href="#s" x="32"/></g></svg>
  <p class="card-text">Suspendisse potenti. Aenean porta tristique sodales. Mauris id ullamcorper purus Suspendisse potenti. Aenean porta tristique sodales.</p>
</div>
<div class="abs card" style="left:266px">
  <div class="card-photo" role="img" aria-label="Modern cabin among trees" style="background:linear-gradient(180deg,#5e7a3a,#3c3a36 50%,#4f8a2e)"></div>
  <div class="card-title">Donec lacinia lacus</div>
  <svg class="stars" width="40" height="8" viewBox="0 0 40 8"><g fill="#f2a51a"><use href="#s"/><use href="#s" x="8"/><use href="#s" x="16"/></g><g fill="none" stroke="#f2a51a" stroke-width=".6"><use href="#s" x="24"/><use href="#s" x="32"/></g></svg>
  <p class="card-text">Suspendisse potenti. Aenean porta tristique sodales. Mauris id ullamcorper purus Suspendisse potenti. Aenean porta tristique sodales.</p>
</div>
<div class="abs card" style="left:412px">
  <div class="card-photo" role="img" aria-label="Ivy covered brick house" style="background:linear-gradient(180deg,#c9d2da,#6d8a4a 35%,#4e6e34 80%,#9a9a90)"></div>
  <div class="card-title">Donec lacinia lacus</div>
  <svg class="stars" width="40" height="8" viewBox="0 0 40 8"><g fill="#f2a51a"><use href="#s"/><use href="#s" x="8"/><use href="#s" x="16"/></g><g fill="none" stroke="#f2a51a" stroke-width=".6"><use href="#s" x="24"/><use href="#s" x="32"/></g></svg>
  <p class="card-text">Suspendisse potenti. Aenean porta tristique sodales. Mauris id ullamcorper purus Suspendisse potenti. Aenean porta tristique sodales.</p>
</div>
<div class="abs card" style="left:557px">
  <div class="card-photo" role="img" aria-label="Bungalow with flower garden and lawn" style="background:linear-gradient(180deg,#dfe6ec,#c9b890 45%,#5e8a30)"></div>
  <div class="card-title">Donec lacinia lacus</div>
  <svg class="stars" width="40" height="8" viewBox="0 0 40 8"><g fill="#f2a51a"><use href="#s"/><use href="#s" x="8"/><use href="#s" x="16"/></g><g fill="none" stroke="#f2a51a" stroke-width=".6"><use href="#s" x="24"/><use href="#s" x="32"/></g></svg>
  <p class="card-text">Suspendisse potenti. Aenean porta tristique sodales. Mauris id ullamcorper purus Suspendisse potenti. Aenean porta tristique sodales.</p>
</div>

<!-- list your property -->
<div class="abs cta" role="img" aria-label="Sunset over rooftops"></div>
<div class="abs cta-title">How To List your Property</div>
<div class="abs cta-sub">Latin words, combined with a handful of model sentence structures</div>
<div class="abs cta-btn">Register</div>

<!-- testimonials -->
<div class="abs section-title" style="left:121px;top:754px;font-size:12.5px">Testimonial</div>
<div class="abs rule" style="left:121px;top:779px;width:264px"></div>

<div class="abs avatar" style="left:124px;top:792px" role="img" aria-label="Client portrait"></div>
<div class="abs item-title" style="left:214px;top:794px">Nullam lacus nunc, gravida</div>
<p class="abs item-text" style="left:214px;top:811px;width:170px">Vestibulumaccumsan egestibulum eu justo convallis augue estas aenean elit intesque sed. Facilispede estibulum nulla orna nisl velit elit ac aliquat non tincidunt.</p>
<div class="abs date" style="left:214px;top:865px"><svg width="7" height="7" viewBox="0 0 7 7"><rect x=".5" y="1" width="6" height="5.5" fill="none" stroke="#999" stroke-width=".7"/><path d="M.5 2.6h6" stroke="#999" stroke-width=".7"/></svg>February 20, 2014</div>

<div class="abs avatar" style="left:124px;top:886px" role="img" aria-label="Client portrait"></div>
<div class="abs item-title" style="left:214px;top:888px">Gravida sit amet rhoncus ornare,</div>
<p class="abs item-text" style="left:214px;top:905px;width:170px">Vestibulumaccumsan egestibulum eu justo convallis augue estas aenean elit intesque sed. Facilispede estibulum nulla orna nisl velit elit ac aliquat non tincidunt.</p>
<div class="abs date" style="left:214px;top:959px"><svg width="7" height="7" viewBox="0 0 7 7"><rect x=".5" y="1" width="6" height="5.5" fill="none" stroke="#999" stroke-width=".7"/><path d="M.5 2.6h6" stroke="#999" stroke-width=".7"/></svg>February 20, 2014</div>

<!-- latest news -->
<div class="abs section-title" style="left:406px;top:752px;font-size:12.5px">Latest News</div>
<div class="abs rule" style="left:406px;top:779px;width:281px"></div>

<div class="abs news-photo" style="left:406px;top:790px;background:linear-gradient(180deg,#8fb5dc,#8a8a86 45%,#6a6a60)" role="img" aria-label="Stone house with turret"></div>
<div class="abs item-title" style="left:515px;top:791px">Duis mollis tempor felis</div>
<div class="abs item-sub" style="left:516px;top:806px">Online Auctions</div>
<p class="abs item-text" style="left:515px;top:824px;width:172px">Vestibulumaccumsan egestibulum eu justo convallis augue estas aenean elit intesque sed. Facilispede estibulum nulla orna nisl velit elit ac aliquat non tincidunt.</p>

<div class="abs news-photo" style="left:406px;top:892px;background:linear-gradient(180deg,#7aa8d8,#e4e4e4 45%,#5d8a3a)" role="img" aria-label="White two storey house"></div>
<div class="abs item-title" style="left:515px;top:893px">Maecenas eu justo rhoncus</div>
<div class="abs item-sub" style="left:515px;top:908px">Online Auctions</div>
<p class="abs item-text" style="left:515px;top:926px;width:172px">Vestibulumaccumsan egestibulum eu justo convallis augue estas aenean elit intesque sed. Facilispede estibulum nulla orna nisl velit elit ac aliquat non tincidunt.</p>

<div class="abs skyline" role="img" aria-label="Faint city skyline"></div>

<!-- newsletter -->
<div class="abs newsletter"></div>
<div class="abs nl-title">Join our newsletter.</div>
<div class="abs nl-sub">Stay up to date with the latest news.</div>
<div class="abs nl-label" style="left:356px">Enter your name</div>
<div class="abs nl-label" style="left:472px">Enter your e-mail</div>
<div class="abs nl-input" style="left:356px"></div>
<div class="abs nl-input" style="left:472px"></div>
<div class="abs nl-btn">Subscribe now</div>

<!-- footer -->
<div class="abs footer"></div>
<div class="abs copyright">©2014 2014 HARROWGATE, ALL RIGHTS RESERVED.</div>
<div class="abs badge" style="left:378px;top:1133px;width:27px;height:20px" aria-label="Partner badge"></div>
<div class="abs badge" style="left:409px;top:1133px;width:18px;height:20px" aria-label="Partner badge"></div>
<div class="abs badge" style="left:432px;top:1133px;width:72px;height:20px" aria-label="Partner badge"></div>
<div class="abs badge" style="left:508px;top:1133px;width:38px;height:20px" aria-label="Partner badge"></div>
<div class="abs badge white" style="left:378px;top:1159px;width:98px;height:25px" aria-label="Partner badge"></div>
<div class="abs badge white" style="left:486px;top:1159px;width:65px;height:25px" aria-label="Partner badge"></div>
<div class="abs foot-social" style="left:639px"></div>
<div class="abs foot-social" style="left:656px"></div>
<div class="abs foot-social" style="left:673px"></div>

</body>
</html>
```